I need a new business card designed, we recently rebranded and I need to get a fresh design to match our new logo, colours and branding.

Details:

Derek Havill | Founder & CEO
Address: 7 Marlowfern Lane, #09-14 Tavenport Crest, Singapore 318547
Tel: +65 93568214
Web: www.frostkarta.com.sg
hello@frostkarta.com.sg

I've attached my old card as well

Industry/Entity Type

Business

Requirements
Must have
• Front and Back
Interesting use of logo
Correct use of colour scheme

```html
<!DOCTYPE html>
<html lang="en">
<head>
<meta charset="utf-8">
<title>Frostkarta Business Card</title>
<link href="https://fonts.googleapis.com/css2?family=Lato:wght@300;400;700;900&display=swap" rel="stylesheet">
<style>
  :root {
    --page-bg: #d9d6d2;
    --brand-blue: #2a9fd8;
    --brand-blue-light: #63b8dd;
    --ink-grey: #5e5a57;
    --ink-dark: #4a4644;
    --card-white: #ececec;
    --circle-white: #f1f1f1;
  }
  * { box-sizing: border-box; margin: 0; padding: 0; }
  html, body { width: 1200px; height: 900px; overflow: hidden; }
  body {
    background: var(--page-bg);
    font-family: "Lato", "Helvetica Neue", Arial, sans-serif;
    display: flex;
    flex-direction: column;
    align-items: center;
    justify-content: center;
    gap: 60px;
  }
  .card {
    width: 560px;
    height: 320px;
    border-radius: 4px;
    box-shadow: 0 6px 18px rgba(0,0,0,0.18);
    position: relative;
    overflow: hidden;
  }

  /* Back side */
  .card-back {
    background: linear-gradient(200deg, var(--brand-blue-light) 0%, var(--brand-blue) 70%);
  }
  .back-mark {
    position: absolute;
    left: 50%;
    top: 52px;
    width: 140px;
    height: 140px;
    margin-left: -70px;
    border-radius: 50%;
    background: var(--circle-white);
    display: flex;
    align-items: center;
    justify-content: center;
    color: var(--brand-blue);
    font-weight: 900;
    font-size: 22px;
  }
  .back-web {
    position: absolute;
    left: 0; right: 0;
    top: 232px;
    text-align: center;
    color: var(--ink-dark);
    font-size: 15px;
    letter-spacing: 1.5px;
  }

  /* Front side */
  .card-front { background: var(--card-white); }
  .front-circle {
    position: absolute;
    left: 44px;
    top: 108px;
    width: 104px;
    height: 104px;
    border-radius: 50%;
    background: var(--brand-blue);
  }
  .front-info {
    position: absolute;
    left: 180px;
    top: 34px;
    right: 24px;
  }
  .brand-name {
    color: var(--ink-grey);
    font-weight: 900;
    font-size: 52px;
    line-height: 1;
    letter-spacing: -1px;
  }
  .brand-tagline {
    color: var(--brand-blue);
    font-weight: 700;
    font-size: 12px;
    letter-spacing: 1.6px;
    text-transform: uppercase;
    margin-top: 4px;
  }
  .person-name {
    color: var(--ink-grey);
    font-weight: 300;
    font-size: 24px;
    letter-spacing: 1px;
    text-transform: uppercase;
    margin-top: 20px;
  }
  .person-title {
    color: var(--ink-grey);
    font-size: 17px;
    margin-top: 2px;
  }
  .contact-list {
    list-style: none;
    margin-top: 14px;
    font-size: 15px;
    color: var(--ink-dark);
    line-height: 1.35;
  }
  .contact-label {
    display: inline-block;
    width: 20px;
    color: var(--brand-blue);
  }
  .address {
    margin-top: 12px;
    font-style: normal;
    font-size: 15px;
    color: var(--ink-dark);
    line-height: 1.35;
  }
</style>
</head>
<body>
  <section class="card card-back" aria-label="Card back">
    <div class="back-mark">frostkarta</div>
    <p class="back-web">www.frostkarta.com.sg</p>
  </section>

  <section class="card card-front" aria-label="Card front">
    <div class="front-circle"></div>
    <div class="front-info">
      <h1 class="brand-name">frostkarta</h1>
      <p class="brand-tagline">Web design &amp; consultancy</p>
      <h2 class="person-name">Derek Havill</h2>
      <p class="person-title">Founder &amp; CEO</p>
      <ul class="contact-list">
        <li><span class="contact-label">T</span>+65 93568214</li>
        <li><span class="contact-label">E</span>hello@frostkarta.com.sg</li>
      </ul>
      <address class="address">7 Marlowfern Lane,<br>#09-14 Tavenport Crest, Singapore 318547</address>
    </div>
  </section>
</body>
</html>
```